Lumavento business card

We need a modern business card - With our 4 colors - See web: www.lumavento.dk

I have attached logo and som old business Cards we have - Lets Make the new ones shine...:-) -

Industry/Entity Type

Business

Requirements
Must have
• the logo with lumavento only,

```html
<!DOCTYPE html>
<html lang="da">
<head>
<meta charset="utf-8">
<title>Lumavento – visitkort</title>
<link rel="stylesheet" href="https://fonts.googleapis.com/css2?family=Source+Sans+3:wght@400;600&display=swap">
<style>
  :root {
    --lime: #8dc63f;
    --orange: #e8843a;
    --pink: #e895c4;
    --purple: #6d2c7a;
    --ink: #3a3a3a;
    --paper: #ffffff;
    --backdrop: #e9e9e9;
  }
  * { margin: 0; padding: 0; box-sizing: border-box; }
  html, body {
    width: 1105px; height: 1200px; overflow: hidden;
    background: var(--backdrop);
    font-family: "Source Sans 3", sans-serif;
  }
  .card {
    position: absolute; left: 192px;
    width: 720px; height: 411px;
    border-radius: 22px; overflow: hidden;
  }
  .card--front { top: 146px; background: var(--paper); }
  .card--back { top: 602px; background: var(--lime); }

  .rings { position: absolute; left: 0; top: 0; }

  .contact {
    position: absolute; left: 36px; top: 212px;
    color: var(--paper); font-size: 19px; line-height: 27.6px;
    list-style: none;
  }
  .contact li { display: flex; align-items: center; }
  .contact .icon { width: 16px; height: 16px; margin-right: 14px; flex: none; }

  .brand {
    position: absolute; left: 430px; width: 254px; text-align: center;
  }
  .brand--front { top: 150px; }
  .brand__name {
    font-size: 22px; letter-spacing: 2px; color: var(--ink); line-height: 30px;
  }
  .brand__rule { height: 2px; background: var(--lime); margin: 8px 0 10px; }
  .brand__tagline { font-size: 15px; color: var(--ink); }

  .person {
    position: absolute; right: 36px; top: 326px; text-align: right;
  }
  .person__name { font-size: 25px; font-weight: 600; color: var(--lime); line-height: 30px; }
  .person__title { font-size: 18px; color: var(--ink); line-height: 26px; }

  .brand--back { left: 392px; width: 304px; top: 296px; }
  .brand--back .brand__name { color: var(--paper); letter-spacing: 4px; }
  .brand--back .brand__rule { background: var(--paper); }
  .brand--back .brand__tagline { color: var(--paper); }
</style>
</head>
<body>
  <section class="card card--front">
    <svg class="rings" width="720" height="411" viewBox="0 0 720 411" aria-hidden="true">
      <circle cx="135" cy="330" r="208" fill="none" stroke="var(--orange)" stroke-width="7"/>
      <circle cx="135" cy="330" r="199" fill="none" stroke="var(--pink)" stroke-width="6"/>
      <circle cx="135" cy="330" r="192" fill="none" stroke="var(--purple)" stroke-width="5"/>
      <circle cx="135" cy="330" r="187" fill="var(--lime)"/>
    </svg>

    <ul class="contact">
      <li>Lindevangs Allé 14</li>
      <li>2000 Frederiksberg</li>
      <li><svg class="icon" viewBox="0 0 16 16"><path fill="#fff" d="M3 1l3 3-1.5 2c1 2 3 4 5 5L11.5 9.5l3 3-2 2.5C6 14 2 9.5 1 3z"/></svg>+45 31 47 20 58</li>
      <li><svg class="icon" viewBox="0 0 16 16"><path fill="#fff" d="M3 1l3 3-1.5 2c1 2 3 4 5 5L11.5 9.5l3 3-2 2.5C6 14 2 9.5 1 3z"/></svg>+45 52 61 83 09</li>
      <li><svg class="icon" viewBox="0 0 16 16"><rect x="1" y="3.5" width="14" height="9" fill="#fff"/><path d="M1 3.5l7 5 7-5" fill="none" stroke="var(--lime)" stroke-width="1.3"/></svg>er@lumavento.dk</li>
      <li><svg class="icon" viewBox="0 0 16 16"><circle cx="8" cy="8" r="7" fill="#fff"/><path d="M5 4c2 1 1 3 3 3s1 3 3 4M4 10c1 0 2 1 2 3" fill="none" stroke="var(--lime)" stroke-width="1.4"/></svg>www.lumavento.dk</li>
    </ul>

    <div class="brand brand--front">
      <p class="brand__name">lumavento</p>
      <div class="brand__rule"></div>
      <p class="brand__tagline">medier til unge</p>
    </div>

    <div class="person">
      <p class="person__name">Maren Holtegaard</p>
      <p class="person__title">Salgsdirektør</p>
    </div>
  </section>

  <section class="card card--back">
    <div class="brand brand--back">
      <p class="brand__name">lumavento</p>
      <div class="brand__rule"></div>
      <p class="brand__tagline">medier til unge</p>
    </div>
  </section>
</body>
</html>
```